PitchTally Webpages and Logo

See attached brief. Take the existing website www.pitchtally.co.uk and logo and transform these assets to:

Give people who arrive on the site for first time the confidence to sign-up easily and quickly
Allow regular returning users quick and easy placing of predictions and encourage them to share the PitchTally prediction on social networks and with their contacts
Convey the essence of a community working together to enjoyably come-up with smart predictions on sporting events
Work seamlessly and well across smartphones, tablets and desktop i.e. Should be Responsive Web Design
Updates

Target Market(s)

Users are sports fans with opinions
Primarily male and early twenties to mid-thirties
They are competitive - they want to beat their peers
Many are from outside the UK

Industry/Entity Type

Events

Logo Text

PitchTally

Coding

Coded - Design and coding required

Number of Pages Required

4 page

Font styles to use
Sans Serif

Requirements
Must have
• Responsive Web Design
• Mobile First
• HTML must work with dedicated bespoke application developed in ASP.NET using MS SQL underneath
• See Brief
Nice to have
• See brief
Should not have
• See brief

```html
<!DOCTYPE html>
<html lang="en">
<head>
<meta charset="utf-8">
<title>PitchTally – Altogether better prediction</title>
<link rel="stylesheet" href="https://fonts.googleapis.com/css2?family=Source+Sans+3:wght@400;600;700&family=Merriweather:wght@700;900&display=swap">
<style>
:root{
  --blue:#3f68a6;
  --blue-band:#4672b2;
  --blue-text:#3a67a8;
  --orange:#f07d1a;
  --orange-dark:#d9680c;
  --green:#7cb82b;
  --header-bg:#f1f1f3;
  --light-bg:#efefef;
  --grey-bg:#e2e2e2;
  --panel-dark:#1f1f21;
  --panel-mid:#29303f;
  --ink:#222;
  --muted:#444;
  --footer:#1c1c1c;
  --sans:"Source Sans 3",Arial,sans-serif;
  --serif:"Merriweather",Georgia,serif;
}
*{box-sizing:border-box;margin:0;padding:0}
html,body{width:702px;height:1200px;overflow:hidden}
body{position:relative;font-family:var(--sans);color:var(--ink);background:#fff}
.abs{position:absolute}

/* top bar */
.topbar{left:0;top:0;width:702px;height:25px;background:var(--blue);color:#fff}
.tagline{left:46px;top:5px;font-size:10.5px}
.kitty{left:430px;top:6px;font-family:var(--serif);font-size:9px;font-weight:700}
.kitty-change{left:494px;top:6px;font-size:8.5px;display:flex;align-items:center;gap:3px}
.btn-top{top:3px;height:16px;font-size:9px;display:flex;align-items:center;justify-content:center;color:#fff;border-radius:2px}
.btn-register{left:541px;width:55px;background:var(--orange)}
.btn-login{left:603px;width:56px;background:var(--green)}

/* header */
.header{left:0;top:25px;width:702px;height:56px;background:var(--header-bg)}
.logo-mark{left:42px;top:11px;width:32px;height:32px;border-radius:50%;border:2px solid #9a9a9a;background:#fff}
.logo-name{left:82px;top:14px;font-family:var(--serif);font-weight:900;font-size:20px;color:var(--blue-text)}
.nav{right:56px;top:26px;display:flex;gap:15px;font-family:var(--serif);font-size:8px;font-weight:700;color:var(--blue-text)}

/* intro */
.intro{left:50px;top:103px;width:400px;font-size:8.2px;line-height:10.5px;font-weight:700;color:var(--blue-text)}
.join{left:481px;top:108px;width:167px;height:26px;background:linear-gradient(#f7921f,var(--orange-dark));color:#fff;font-family:var(--serif);font-weight:900;font-size:13px;display:flex;align-items:center;justify-content:center;border-radius:2px}

/* hero */
.hero{left:0;top:163px;width:702px;height:303px;background:var(--blue-band)}
.hero-photo{left:56px;top:186px;width:362px;height:248px;background:radial-gradient(ellipse at 65% 25%,#f0b34a 0%,#b8641f 30%,#4a2a18 65%,#140d0a 100%)}
.hero-caption{left:56px;top:376px;width:362px;height:38px;background:rgba(0,0,0,.55)}
.hero-title{left:83px;top:382px;font-size:19px;color:#fff}
.share{top:387px;height:17px;font-size:8px;color:#fff;display:flex;align-items:center;gap:4px;padding:0 6px}
.share-fb{left:275px;width:58px;background:#4267a8}
.share-tw{left:337px;width:58px;background:#1da1e0}
.share i{display:block;width:6px;height:6px;background:#fff}
.stats{left:422px;top:186px;width:226px;height:248px;background:var(--panel-dark)}
.stat-head,.stat-sub{left:422px;width:226px;display:flex;align-items:center;justify-content:center;color:#fff}
.stat-head{font-size:14px;gap:32px}
.stat-sub{background:var(--panel-mid);font-size:7.5px;color:#dfe3ea}

/* how it works */
.how{left:0;top:466px;width:702px;height:152px;background:var(--light-bg)}
.section-title{left:0;width:702px;text-align:center}
.how-title{top:480px;font-size:18px}
.step-icon{top:522px;width:44px;height:44px;border-radius:50%;background:var(--orange);display:flex;align-items:center;justify-content:center}
.step-name{top:526px;font-size:13px}
.step-text{top:546px;width:120px;font-size:6.6px;line-height:9.2px;font-weight:700;color:var(--muted)}

/* predict */
.predict-title{top:637px;font-family:var(--serif);font-weight:700;font-size:13.5px;color:#555}
.crest{top:697px;width:26px;height:32px;border-radius:3px 3px 13px 13px}
.team{top:736px;width:110px;text-align:center;font-size:8px;color:#333}
.kick{top:759px;width:200px;text-align:center;font-size:9px;font-weight:700}
.vs{top:710px;font-size:8px}
.predict-btn{top:782px;width:104px;height:18px;background:var(--orange);color:#fff;font-size:8px;display:flex;align-items:center;justify-content:center}

/* testimonials */
.testimonials{left:0;top:832px;width:702px;height:294px;background:var(--grey-bg)}
.test-title{top:845px;font-size:13px}
.portrait{top:882px;width:86px;height:100px}
.portrait.active{border:2px solid var(--orange)}
.person{top:991px;width:86px;text-align:center;font-size:8px}
.quote{left:139px;top:1014px;width:424px;height:96px;background:#d2d2d2;border:1px solid #c3c3c3;padding:12px 24px;font-size:6.6px;line-height:9px;text-align:center;color:#333}
.quote-notch{left:174px;top:1007px}

/* footer */
.footer{left:0;top:1126px;width:702px;height:74px;background:var(--footer)}
.footer-links{left:0;top:1141px;width:702px;display:flex;justify-content:center;gap:11px;font-size:8px;color:#9a9a9a}
.social{top:1158px;width:16px;height:16px;border-radius:50%;background:#fff}
.copyright{top:1181px;font-size:7px;color:#8a8a8a}
</style>
</head>
<body>

<div class="abs topbar"></div>
<div class="abs tagline" style="color:#fff">Altogether better prediction</div>
<div class="abs kitty" style="color:#fff">Kitty : £1289</div>
<div class="abs kitty-change" style="color:#fff">
  <svg width="8" height="8" viewBox="0 0 8 8"><path d="M4 0L8 4H5.3V8H2.7V4H0Z" fill="#8bd13a"/></svg>3%
</div>
<div class="abs btn-top btn-register">Register</div>
<div class="abs btn-top btn-login">Login</div>

<header class="abs header">
  <div class="abs logo-mark"></div>
  <div class="abs logo-name">PitchTally</div>
  <nav class="abs nav"><span>Home</span><span>About</span><span>MiniLiga</span><span>Tables</span><span>Kitty</span><span>FAQ</span><span>Me</span></nav>
</header>

<p class="abs intro">Predict results, scores and scorers for your free chance to win a £20 ShopNest voucher every week. Overall season winner gets up to £1000 in ShopNest vouchers! No entry fee and no catches.</p>
<div class="abs join">Join Now</div>

<section class="abs hero"></section>
<div class="abs hero-photo" role="img" aria-label="Concert crowd with raised hands under warm stage lights"></div>
<div class="abs hero-caption"></div>
<div class="abs hero-title">PitchTally Hot Tips</div>
<div class="abs share share-fb"><i></i>Share 45</div>
<div class="abs share share-tw"><i></i>Tweet 45</div>

<div class="abs stats"></div>
<div class="abs stat-head" style="top:186px;height:39px"><span>RESULT</span><span>100%</span></div>
<div class="abs stat-sub" style="top:225px;height:35px">REDBRIDGE UNITED WIN</div>
<div class="abs stat-head" style="top:260px;height:46px"><span>SCORE</span><span>43%</span></div>
<div class="abs stat-sub" style="top:306px;height:36px">ASHFORD VALE 0 REDBRIDGE UNITED 2</div>
<div class="abs stat-head" style="top:342px;height:46px"><span>1st GOAL</span><span>80%</span></div>
<div class="abs stat-sub" style="top:388px;height:36px">Rowan D</div>

<section class="abs how"></section>
<h2 class="abs section-title how-title" style="font-weight:400">How it works</h2>

<div class="abs step-icon" style="left:68px">
  <svg width="16" height="16" viewBox="0 0 16 16"><path d="M5 7V4.5a3 3 0 0 1 6 0" fill="none" stroke="#fff" stroke-width="1.8"/><rect x="3" y="7" width="10" height="8" rx="1" fill="#fff"/></svg>
</div>
<div class="abs step-name" style="left:128px">Login</div>
<p class="abs step-text" style="left:128px">Duis aute irure dolor in reprehen-derit in voluptate velit esse cillum dolore eu fugiat nulla.</p>

<div class="abs step-icon" style="left:260px">
  <svg width="18" height="16" viewBox="0 0 18 16"><path d="M1 1V15H17" fill="none" stroke="#fff" stroke-width="1.5"/><path d="M3 12L7 7L10 10L16 4" fill="none" stroke="#fff" stroke-width="1.8"/><path d="M12.5 3.5H16.5V7.5" fill="none" stroke="#fff" stroke-width="1.5"/></svg>
</div>
<div class="abs step-name" style="left:320px">Predict Score</div>
<p class="abs step-text" style="left:320px">Duis aute irure dolor in reprehen-derit in voluptate velit esse cillum dolore eu fugiat nulla.</p>

<div class="abs step-icon" style="left:452px">
  <svg width="18" height="18" viewBox="0 0 18 18"><path d="M17 1L1 8L7 10L9 17Z" fill="#fff"/><path d="M17 1L7 10" stroke="#f07d1a" stroke-width="1.2"/></svg>
</div>
<div class="abs step-name" style="left:512px">Enjoy</div>
<p class="abs step-text" style="left:512px">Duis aute irure dolor in reprehen-derit in voluptate velit esse cillum dolore eu fugiat nulla.</p>

<h2 class="abs section-title predict-title">Predict Score</h2>

<div class="abs crest" style="left:91px;background:#7aa7d6"></div>
<div class="abs vs" style="left:143px">v</div>
<div class="abs crest" style="left:179px;background:#c8333c"></div>
<div class="abs team" style="left:49px">Northgate City</div>
<div class="abs team" style="left:137px">Harbour Palace</div>
<div class="abs kick" style="left:39px">Sat 20 Dec 2014 12:45 PM</div>
<div class="abs predict-btn" style="left:88px">Predict Score Now</div>

<div class="abs crest" style="left:290px;background:#7a2a45"></div>
<div class="abs vs" style="left:341px">v</div>
<div class="abs crest" style="left:371px;background:#d5261f"></div>
<div class="abs team" style="left:248px">Ashford Vale</div>
<div class="abs team" style="left:329px;top:738px">Redbridge United</div>
<div class="abs kick" style="left:252px">Sat 20 Dec 2014 3:00 PM</div>
<div class="abs predict-btn" style="left:300px">Predict Score Now</div>

<div class="abs crest" style="left:477px;background:#2f5ea8"></div>
<div class="abs vs" style="left:533px">v</div>
<div class="abs crest" style="left:573px;background:#1f3f78"></div>
<div class="abs team" style="left:434px;width:110px">Kingsway Park Rangers</div>
<div class="abs team" style="left:530px">Westmoor Albion</div>
<div class="abs kick" style="left:433px">Sat 20 Dec 2014 12:45 PM</div>
<div class="abs predict-btn" style="left:482px">Predict Score Now</div>

<section class="abs testimonials"></section>
<h2 class="abs section-title test-title" style="font-weight:400">Testimonials</h2>

<div class="abs portrait active" style="left:140px;background:linear-gradient(#bdbdbd,#6a6a6a)" role="img" aria-label="Portrait photo of Dave"></div>
<div class="abs portrait" style="left:252px;background:linear-gradient(#c9c9c9,#9a9a9a)" role="img" aria-label="Portrait photo of Lara"></div>
<div class="abs portrait" style="left:363px;background:linear-gradient(#b8b8b8,#5f5f5f)" role="img" aria-label="Portrait photo of Kristofer"></div>
<div class="abs portrait" style="left:476px;background:linear-gradient(#b5b5b5,#777)" role="img" aria-label="Portrait photo of Juliya"></div>
<div class="abs person" style="left:141px">DAVE</div>
<div class="abs person" style="left:252px">LARA</div>
<div class="abs person" style="left:363px">KRISTOFER</div>
<div class="abs person" style="left:476px">JULIYA</div>

<div class="abs quote">Temporibus autem quibusdam et aut officiis debitis aut rerum necessitatibus saepe eveniet ut et voluptates repudiandae sint et molestiae non recusandae. But in certain circumstances and owing to the claims of duty or the obligations of business it will frequently occur that pleasures have to be repudiated and annoyances accepted. The wise man therefore always holds in these matters to this principle of selection: he rejects pleasures to secure other greater pleasures, or else he endures pains to avoid worse pains</div>
<svg class="abs quote-notch" width="16" height="8" viewBox="0 0 16 8"><path d="M0 8L8 0L16 8Z" fill="#d2d2d2"/><path d="M0 8L8 0L16 8" fill="none" stroke="#c3c3c3"/></svg>

<footer class="abs footer"></footer>
<nav class="abs footer-links"><span>FAQ</span><span>Profile</span><span>History</span><span>Mini-liga Admin</span><span>About</span><span>Contact</span><span>Privacy</span><span>Terms</span></nav>
<div class="abs social" style="left:322px"></div>
<div class="abs social" style="left:343px"></div>
<div class="abs social" style="left:364px"></div>
<div class="abs section-title copyright">© 2014. www.pitchtally.co.uk</div>

</body>
</html>
```